Brookvane Consulting Business Card Design

Business Card Design for Brookvane Consulting. Brookvane Consulting is a boutique consultancy based in Atlanta, GA., that specializes in marketing strategy, organization planning, and leadership development. We provide solutions for small businesses and startups as well as Vantage 300 companies.

http://brookvaneconsulting.com/

Target Market(s)

We provide solutions for small businesses and startups as well as Vantage 300 companies.

Industry/Entity Type

Consulting

Contact Information for Business Card

Two sided business card with priority on contact information, logo, tag line (Inspiration to Dream More, Do More, Become More)

Colors

Designer to choose colors to be used in the design.

Requirements
Must have
• contact information, logo, tag line (Inspiration to Dream More, Do More, Become More)
• Simple no over communication.
Nice to have
• I would like to see different placements of logo and creative use of both sides of the card
Should not have
• Do not put too much information on the card.

```html
<!DOCTYPE html>
<html lang="en">
<head>
<meta charset="utf-8">
<title>Brookvane Consulting Business Card</title>
<link href="https://fonts.googleapis.com/css2?family=Montserrat:wght@400;500;600&display=swap" rel="stylesheet">
<style>
  :root {
    --backdrop: #3a302b;
    --card: #141414;
    --card-edge: #1d1d1d;
    --ink: #f2f2f2;
    --ink-soft: #d6d6d6;
    --ink-muted: #b4b4b4;
  }
  * { margin: 0; padding: 0; box-sizing: border-box; }
  html, body {
    width: 1200px; height: 715px; overflow: hidden;
    background: var(--backdrop);
    font-family: "Montserrat", sans-serif;
  }
  .canvas {
    position: relative; width: 1200px; height: 715px;
    display: flex; align-items: center; justify-content: center; gap: 50px;
  }
  .card {
    width: 525px; height: 300px;
    background: linear-gradient(135deg, var(--card-edge), var(--card));
    border-radius: 6px;
    box-shadow: 0 14px 30px rgba(0,0,0,0.45);
    color: var(--ink);
    position: relative;
    overflow: hidden;
  }
  .card--front {
    display: flex; flex-direction: column; align-items: center; justify-content: center;
  }
  .brand {
    display: flex; align-items: center; gap: 12px;
    font-weight: 600; letter-spacing: 1px; color: var(--ink);
  }
  .brand__mark {
    width: 14px; height: 14px; background: var(--ink); flex: none;
  }
  .card--front .brand { font-size: 32px; }
  .front__tagline {
    margin-top: 16px; font-size: 12px; letter-spacing: 1px; color: var(--ink-muted);
  }
  .front__url {
    margin-top: 30px; font-size: 14px; letter-spacing: 1.5px; color: var(--ink-soft);
  }
  .card--back {
    display: flex; align-items: center; padding: 0 26px 0 30px;
  }
  .card--back .brand {
    font-size: 19px; width: 190px; flex: none; flex-wrap: wrap; line-height: 1.3;
  }
  .divider {
    width: 1px; height: 200px; background: var(--ink); margin: 0 22px 0 8px; flex: none;
  }
  .contact { min-width: 0; }
  .contact__name {
    font-size: 17px; font-weight: 500; letter-spacing: 1.5px; text-transform: uppercase;
  }
  .contact__role { font-size: 12px; color: var(--ink-soft); margin-top: 3px; }
  .contact__address { font-size: 12px; line-height: 1.45; margin-top: 14px; }
  .contact__list { list-style: none; margin-top: 10px; font-size: 12px; line-height: 1.7; }
  .contact__list li { display: flex; align-items: center; gap: 8px; white-space: nowrap; }
  .contact__list svg { width: 11px; height: 11px; flex: none; fill: none; stroke: var(--ink); stroke-width: 1.6; }
</style>
</head>
<body>
<main class="canvas">
  <section class="card card--front">
    <div class="brand"><span class="brand__mark"></span>Brookvane Consulting</div>
    <p class="front__tagline">Inspiration to Dream More, Do More, Become More</p>
    <p class="front__url">www.brookvaneconsulting.com</p>
  </section>

  <section class="card card--back">
    <div class="brand"><span class="brand__mark"></span>Brookvane Consulting</div>
    <div class="divider"></div>
    <div class="contact">
      <p class="contact__name">Daniel Harrow</p>
      <p class="contact__role">Managing Director</p>
      <p class="contact__address">1140 Lakeview Ave NE, Suite 22B<br>Atlanta, GA</p>
      <ul class="contact__list">
        <li><svg viewBox="0 0 12 12"><path d="M2 1.5h2.5l1 2.5-1.5 1a6 6 0 0 0 3 3l1-1.5 2.5 1V11A9 9 0 0 1 1 2.5z"/></svg>555-013-2468</li>
        <li><svg viewBox="0 0 12 12"><rect x="1" y="2.5" width="10" height="7"/><path d="M1 2.5l5 4 5-4"/></svg>dana@brookvaneconsulting.com</li>
        <li><svg viewBox="0 0 12 12"><circle cx="6" cy="6" r="5"/><path d="M1 6h10M6 1c-2.5 3-2.5 7 0 10M6 1c2.5 3 2.5 7 0 10"/></svg>www.brookvaneconsulting.com</li>
      </ul>
    </div>
  </section>
</main>
</body>
</html>
```